Venture 482 - Lumora Book Cover

I am looking for a Lumora book cover for my book about "Venture 482".
The Book is Titled:
Venture 482 Ascended
Shaping Outcomes: Paths To Unlocking Cosmic Truths
Author is Dorian Pell
Here is a book description that may help you understand more about it:
Inspired by the genius of Edwin Marlowe, this comprehensive guide delves into the ancient wisdom and cutting-edge science behind the 482 method, a powerful tool for manifesting your desires. Whether you're seeking personal growth, financial success, or spiritual enlightenment, this book provides advanced techniques and methods to transform your dreams into reality.
Any questions please ask.
Thanks
Owen

```html
<!DOCTYPE html>
<html lang="en">
<head>
<meta charset="utf-8">
<title>Venture 482 Ascended – Book Cover</title>
<link rel="stylesheet" href="https://fonts.googleapis.com/css2?family=Cinzel:wght@400;500&family=Tinos&display=swap">
<style>
  :root {
    --ink-cream: #f7ebdf;
    --glow-copper: rgba(197, 138, 92, 0.22);
    --night-deep: #120f2a;
    --night-violet: #3a2a66;
  }
  * { margin: 0; padding: 0; box-sizing: border-box; }
  html, body {
    width: 805px; height: 1200px; overflow: hidden;
    background: var(--night-deep);
  }
  .cover {
    position: relative;
    width: 805px; height: 1200px;
    overflow: hidden;
    color: var(--ink-cream);
  }
  .cover-art {
    position: absolute; inset: 0;
    background:
      radial-gradient(ellipse 150px 180px at 50% 70%, rgba(184,117,46,0.55), transparent 70%),
      radial-gradient(ellipse 260px 200px at 50% 92%, rgba(138,47,42,0.45), transparent 75%),
      radial-gradient(ellipse 170px 230px at 50% 18%, rgba(10,8,24,0.85), transparent 75%),
      radial-gradient(ellipse 260px 420px at 50% 55%, rgba(18,14,36,0.7), transparent 75%),
      radial-gradient(ellipse 260px 320px at 88% 30%, rgba(70,100,190,0.7), transparent 70%),
      radial-gradient(ellipse 240px 320px at 10% 35%, rgba(110,60,140,0.6), transparent 70%),
      radial-gradient(ellipse 200px 160px at 60% 8%, rgba(190,200,230,0.35), transparent 70%),
      linear-gradient(180deg, var(--night-violet) 0%, #2c2558 45%, #1b1740 80%, var(--night-deep) 100%);
  }
  .title-glow {
    position: absolute; left: 140px; top: 440px;
    width: 525px; height: 300px;
    background: radial-gradient(ellipse at 50% 50%, var(--glow-copper), transparent 70%);
  }
  .series-title {
    position: absolute; left: 0; right: 0; top: 318px;
    text-align: center;
    font-family: "Cinzel", serif;
    font-weight: 400;
    font-size: 104px;
    line-height: 1;
    letter-spacing: 0.01em;
  }
  .series-number {
    position: absolute; top: 482px;
    font-family: "Cinzel", serif;
    font-weight: 400;
    font-size: 232px;
    line-height: 1;
    width: 172px; text-align: center;
  }
  .series-number.n1 { left: 140px; }
  .series-number.n2 { left: 316px; }
  .series-number.n3 { left: 492px; }
  .edition {
    position: absolute; left: 0; right: 0; top: 757px;
    text-align: center;
    font-family: "Cinzel", serif;
    font-size: 40px;
    letter-spacing: 0.86em;
    padding-left: 0.86em;
    line-height: 1;
  }
  .subtitle {
    position: absolute; left: 0; right: 0; top: 874px;
    text-align: center;
    font-family: "Tinos", serif;
  }
  .subtitle-lead {
    font-size: 27px;
    text-transform: uppercase;
    line-height: 1;
  }
  .subtitle-body {
    margin-top: 18px;
    font-size: 25px;
    line-height: 32px;
  }
  .author {
    position: absolute; left: 0; right: 0; top: 1076px;
    text-align: center;
    font-family: "Cinzel", serif;
    font-size: 46px;
    letter-spacing: 0.36em;
    padding-left: 0.36em;
    line-height: 1;
    text-transform: uppercase;
  }
</style>
</head>
<body>
<main class="cover">
  <div class="cover-art" role="img" aria-label="Dreamlike illustration of a meditating figure in silhouette with visible anatomy, surrounded by swirling violet, blue and gold cosmic clouds and flowing line patterns"></div>
  <div class="title-glow" role="img" aria-label="Decorative copper ornament framing the title number"></div>

  <h1 class="series-title">Venture</h1>
  <div class="series-number n1">4</div>
  <div class="series-number n2">8</div>
  <div class="series-number n3">2</div>
  <p class="edition">Ascended</p>

  <div class="subtitle">
    <p class="subtitle-lead">Shaping Outcomes:</p>
    <p class="subtitle-body">Paths to unlocking<br>cosmic truths</p>
  </div>

  <p class="author">Dorian Pell</p>
</main>
</body>
</html>
```